3D Printing Website redesign

We are in the process of redesigning our website. Attached is an image of one of the proposed pages - "The Quillmarrow". The idea with this page is that site visitors can get an indicative estimate of the cost of 3D Printing based on some provided metrics. When the user alters the metrics the price changes accordingly. We are looking for a design to support this page that will also be used across our site.

Reason: Allow more time for designers to submit designs

Reason: Still looking for the design to blow us away!

Printing

```html
<!DOCTYPE html>
<html lang="en">
<head>
<meta charset="utf-8">
<title>Layerforge Print Lab – Training</title>
<link rel="stylesheet" href="https://fonts.googleapis.com/css2?family=PT+Sans:wght@400;700&family=Encode+Sans+Condensed:wght@500&display=swap">
<style>
  :root {
    --page-bg: #f3f3f3;
    --nav-blue: #244a88;
    --nav-active: #00aeef;
    --nav-divider: #1c3c72;
    --search-bg: #e3e4ee;
    --contact-grey: #8a8a8a;
    --text-dark: #222;
    --heading: #333;
    --crumb-home: #29abe2;
    --crumb-2: #3c5fc0;
    --crumb-3: #4a68c4;
    --crumb-4: #111536;
    --frame: #cfcfcf;
    --placeholder: #d3d3d3;
    --footer-bg: #444;
    --white: #fff;
  }
  html, body {
    margin: 0; padding: 0;
    width: 1200px; height: 888px; overflow: hidden;
  }
  body { background: var(--page-bg); font-family: "PT Sans", sans-serif; }
  .page {
    position: relative; width: 1200px; height: 888px; overflow: hidden;
    background: var(--page-bg);
  }
  .contact {
    position: absolute; left: 126px; top: 11px; margin: 0;
    font-size: 15px; line-height: 17.5px; color: var(--contact-grey);
  }
  .account-button {
    position: absolute; left: 1047px; top: 0; width: 50px; height: 47px;
    background: var(--nav-blue); display: flex; align-items: center; justify-content: center;
  }
  .search {
    position: absolute; left: 872px; top: 58px; width: 225px; height: 47px;
    background: var(--search-bg); border: 1px solid var(--nav-blue); box-sizing: border-box;
    display: flex; align-items: center; justify-content: space-between;
    padding: 0 16px 0 18px; font-size: 15px; color: #2a2a3a;
  }
  .main-nav {
    position: absolute; left: 0; top: 112px; width: 1200px; height: 57px;
    background: var(--nav-blue); box-shadow: 0 3px 3px rgba(0,0,0,0.25);
  }
  .main-nav a {
    position: absolute; top: 0; height: 57px; line-height: 57px;
    color: var(--white); text-decoration: none; font-size: 15px; text-align: center;
    border-left: 1px solid var(--nav-divider); box-sizing: border-box;
  }
  .main-nav a.active { background: var(--nav-active); }
  .brand {
    position: absolute; left: 488px; top: 8px; width: 200px; height: 200px;
    border-radius: 50%; background: var(--white);
    box-shadow: 0 4px 10px rgba(0,0,0,0.25);
    display: flex; align-items: center; justify-content: center;
    font-size: 28px; font-weight: 700; color: var(--nav-blue);
  }
  .breadcrumb { position: absolute; left: 103px; top: 248px; }
  .breadcrumb text { font-family: "PT Sans", sans-serif; font-size: 15px; fill: var(--white); letter-spacing: 0.5px; }
  .page-title {
    position: absolute; left: 103px; top: 303px; margin: 0;
    font-family: "Encode Sans Condensed", sans-serif; font-weight: 500;
    font-size: 26px; line-height: 36px; color: var(--heading);
  }
  .copy p {
    position: absolute; left: 100px; margin: 0;
    font-size: 12px; line-height: 20px; letter-spacing: -0.2px; color: var(--text-dark);
  }
  .copy .narrow { width: 645px; }
  .copy .wide { width: 994px; }
  .feature-image {
    position: absolute; left: 750px; top: 352px; width: 344px; height: 261px;
    border: 1px solid var(--frame); box-sizing: border-box; background: var(--white); padding: 5px;
  }
  .feature-image div { width: 100%; height: 100%; background: var(--placeholder); }
  .divider {
    position: absolute; left: 130px; top: 808px; width: 940px;
    border-top: 1px dashed #cfcfcf;
  }
  .site-footer {
    position: absolute; left: 0; top: 838px; width: 1200px; height: 50px;
    background: var(--footer-bg); overflow: hidden;
  }
  .site-footer h3 {
    position: absolute; top: 28px; margin: 0; font-weight: 400;
    font-size: 23px; line-height: 28px; color: var(--white);
  }
</style>
</head>
<body>
<div class="page">
  <header>
    <p class="contact">Layerforge Print Lab<br>Unit 12, 45 Harbour Lane, Millbrook 2190<br>Ph: 61 2 5550 1842<br>M: 0400 555 019<br>e-mail: hello@layerforgeprint.example</p>
    <div class="account-button" aria-label="Account">
      <svg width="22" height="22" viewBox="0 0 22 22"><circle cx="11" cy="6.5" r="5" fill="#fff"/><path d="M1 21c0-6 4-9 10-9s10 3 10 9z" fill="#fff"/></svg>
    </div>
    <div class="search"><span>Search...</span>
      <svg width="18" height="18" viewBox="0 0 18 18"><circle cx="7.5" cy="7.5" r="6" fill="none" stroke="#222" stroke-width="2"/><path d="M12 12l5 5" stroke="#222" stroke-width="2.4"/></svg>
    </div>
    <nav class="main-nav">
      <a href="#" style="left:102px;width:77px">HOME</a>
      <a href="#" style="left:178px;width:80px">SHOP</a>
      <a href="#" style="left:257px;width:89px">PRICES</a>
      <a href="#" style="left:345px;width:111px">MATERIALS</a>
      <a href="#" style="left:694px;width:106px;border-left:0">GALLERY</a>
      <a href="#" class="active" style="left:800px;width:105px">TRAINING</a>
      <a href="#" style="left:905px;width:112px">ABOUT US</a>
      <a href="#" style="left:1017px;width:81px;border-right:1px solid var(--nav-divider)">BLOG</a>
    </nav>
    <div class="brand">Layerforge</div>
  </header>

  <main>
    <svg class="breadcrumb" width="426" height="32" viewBox="0 0 426 32" aria-label="Breadcrumb">
      <polygon points="297,0 425,0 425,32 297,32 311,16" fill="var(--crumb-4)"/>
      <polygon points="174,0 297,0 311,16 297,32 174,32 188,16" fill="var(--crumb-3)"/>
      <polygon points="50,0 174,0 188,16 174,32 50,32 64,16" fill="var(--crumb-2)"/>
      <polygon points="0,0 50,0 64,16 50,32 0,32" fill="var(--crumb-home)"/>
      <path d="M27 6l-12 10h3v8h6v-6h6v6h6v-8h3z" fill="#fff"/>
      <text x="95" y="22">LEVEL 2</text>
      <text x="219" y="22">LEVEL 3</text>
      <text x="343" y="22">LEVEL 4</text>
    </svg>

    <h1 class="page-title">Sed gravida ligula luctus sed</h1>

    <div class="feature-image" role="img" aria-label="Feature photo of a 3D printing training session"><div></div></div>

    <div class="copy">
      <p class="narrow" style="top:348px">Lorem ipsum dolor sit amet, consectetur adipiscing elit. Sed interdum nisi id eleifend ornare. Vivamus varius, nulla et tempus adipiscing, neque est pellentesque arcu, id pellentesque augue nibh ut lacus. Maecenas eu diam eu libero interdum suscipit. Fusce laoreet id odio a rhoncus. Ut gravida elit non lorem dapibus, in ornare libero porta. Integer elementum ligula in tempor scelerisque. Cras dictum eleifend nisi, ut ullamcorper nibh imperdiet eu. Nam ut est lacus. Curabitur mattis tellus a eros fringilla bibendum. Morbi sit amet scelerisque augue. Nullam sit amet lacus arcu. Nam vel nisl non mauris molestie ultrices.</p>
      <p class="narrow" style="top:468px">Aliquam posuere condimentum mi eget commodo. Praesent feugiat eget magna et porttitor. Praesent sed tristique orci. Nam sodales ante in iaculis consequat. Nullam mattis dolor nunc, ac ullamcorper purus tempus sit amet. Ut non nibh a leo sodales rhoncus nec et felis. Nullam malesuada sagittis rhoncus. In rhoncus, quam non consectetur pulvinar, lorem odio imperdiet arcu, id fringilla ligula ipsum non velit. Donec a urna a neque volutpat tempus. Suspendisse tincidunt turpis id augue fringilla, a consectetur nisl mattis. Nullam at euismod elit. Nullam at ultricies purus. Aliquam blandit a felis at hendrerit. Nam luctus massa in justo pellentesque accumsan. Nunc consequat volutpat augue, in pulvinar felis auctor non. Cras volutpat vehicula eros, consectetur congue justo pretium vel.</p>
      <p class="wide" style="top:628px">Maecenas at eros eu turpis consectetur commodo. Nam porttitor mollis cursus. Aliquam pretium semper sapien a pretium. Vestibulum vel lacus eget lorem auctor dapibus posuere nec ipsum. Integer cursus velit at dui vulputate, at lobortis metus vulputate. Donec ornare vestibulum felis, vulputate dictum nisl iaculis id. Aliquam suscipit dictum dui, eget viverra lorem accumsan a. Suspendisse at tortor lorem. Vestibulum id massa non magna iaculis convallis. Duis auctor, dui elementum suscipit pretium, odio mi tempus diam, nec blandit leo nisi eu est. Nullam nec nisi semper libero scelerisque aliquam. Cras dictum feugiat posuere. Etiam volutpat iaculis tincidunt. Vestibulum ante ipsum primis in faucibus orci luctus et ultrices posuere cubilia Curae;</p>
      <p class="wide" style="top:728px">Proin condimentum, ante in porta dapibus, mauris libero vestibulum lorem, et porttitor mi diam nec massa. Phasellus ac est pulvinar, pulvinar purus sed, mattis erat. Morbi tincidunt viverra velit, vel vulputate arcu vulputate nec. Aenean dignissim purus in sapien tempus, sed interdum lectus scelerisque. Praesent scelerisque aliquam gravida. Vestibulum aliquet vitae sem eu hendrerit. Aliquam diam felis, fermentum a laoreet vitae, cursus a mauris. In hac habitasse platea dictumst.</p>
    </div>

    <div class="divider"></div>
  </main>

  <footer class="site-footer">
    <h3 style="left:128px">About Us</h3>
    <h3 style="left:378px">Pages</h3>
    <h3 style="left:627px">Recent Posts</h3>
    <h3 style="left:877px">Connect with Us</h3>
  </footer>
</div>
</body>
</html>
```